****Business Card Design for Quarrystone Development. Design based around attached logo/company name

I’m looking for business card design for my company Quarrystone Development Group,LLC. Design should be professional, sharp and minimal. Outside of the attached logos, greyscale colors for remainder of cards. My thoughts are two-sided card with attached logo on one side and my info on the other but open to one-sided as well with right design.
Target Market(s)
Real estate professionals including banks, private investors, property owners, developers, commercial tenants like Brewlantern, Grovika or Tanquist’s.
Industry/Entity Type
Commercial real estate development and investments.
Contact Information for Business Card
Name, title, email, phone #’s, web address and physical address
Font styles to use
Other font styles liked:
- Helvetica, Garamond, etc
Colors
Designer to choose only greyscale colors for use in the design.
Requirements
Must have
- Attached logo first or second options.
Nice to have
- Two sided card with logo on one side. Attached Logo/company name can be laid out any way that flows as long as it’s legible.name
Should not have
- No loud colors. ***Please do not include logo, I have removed the company design with a logo image.

```html
<!DOCTYPE html>
<html lang="en">
<head>
<meta charset="utf-8">
<title>Quarrystone Development – Business Card</title>
<link href="https://fonts.googleapis.com/css2?family=Tinos&display=swap" rel="stylesheet">
<style>
  :root {
    --backdrop: #c8c8c8;
    --front-top: #7b8293;
    --front-bottom: #5b6374;
    --back-top: #515664;
    --back-bottom: #343945;
    --ink: #ffffff;
    --ink-soft: rgba(255,255,255,0.92);
    --divider: rgba(255,255,255,0.55);
  }
  html, body {
    margin: 0;
    width: 1200px;
    height: 1200px;
    overflow: hidden;
    background: var(--backdrop);
  }
  .canvas {
    position: relative;
    width: 1200px;
    height: 1200px;
    font-family: "Tinos", "Times New Roman", serif;
    color: var(--ink);
  }
  .card {
    position: absolute;
    left: 262px;
    width: 686px;
    box-sizing: border-box;
  }
  .card--front {
    top: 165px;
    height: 392px;
    background: linear-gradient(180deg, var(--front-top), var(--front-bottom) 97%);
  }
  .card__stripe {
    position: absolute;
    left: 0;
    right: 0;
    bottom: 0;
    height: 12px;
    background: var(--ink);
  }
  .brand {
    position: absolute;
    left: 80px;
    top: 160px;
    width: 260px;
    text-align: right;
  }
  .brand__name {
    font-size: 31px;
    letter-spacing: 0.5px;
    line-height: 1;
  }
  .brand__tagline {
    font-size: 13px;
    letter-spacing: 0.3px;
    margin-top: 2px;
  }
  .card__divider {
    position: absolute;
    left: 357px;
    top: 96px;
    width: 1px;
    height: 206px;
    background: linear-gradient(180deg, transparent, var(--divider) 20%, var(--divider) 80%, transparent);
  }
  .contact {
    position: absolute;
    left: 387px;
    top: 104px;
    font-size: 16px;
    color: var(--ink-soft);
  }
  .contact__name {
    font-size: 22px;
    letter-spacing: 0.5px;
    color: var(--ink);
    line-height: 1.1;
  }
  .contact__title { line-height: 1.3; }
  .contact__address {
    margin-top: 12px;
    line-height: 20px;
  }
  .contact__list {
    list-style: none;
    margin: 12px 0 0;
    padding: 0;
  }
  .contact__item {
    display: flex;
    align-items: center;
    height: 20.7px;
  }
  .contact__icon {
    width: 14px;
    height: 14px;
    margin-right: 11px;
    fill: var(--ink);
  }
  .card--back {
    top: 626px;
    height: 391px;
    background: linear-gradient(180deg, var(--back-top), var(--back-bottom));
  }
  .back-mark {
    position: absolute;
    left: 0;
    right: 0;
    top: 168px;
    text-align: center;
    font-size: 30px;
    letter-spacing: 4px;
  }
  .back-web {
    position: absolute;
    left: 0;
    right: 0;
    top: 315px;
    text-align: center;
    font-size: 15px;
    letter-spacing: 6.5px;
  }
</style>
</head>
<body>
<div class="canvas">
  <section class="card card--front">
    <div class="brand">
      <div class="brand__name">QUARRYSTONE</div>
      <div class="brand__tagline">DEVELOPMENT GROUP, LLC</div>
    </div>
    <div class="card__divider"></div>
    <div class="contact">
      <div class="contact__name">DANIEL HARTWELL</div>
      <div class="contact__title">President</div>
      <div class="contact__address">4120 Alder Crest Way<br>Anchorage, Alaska 99508</div>
      <ul class="contact__list">
        <li class="contact__item">
          <svg class="contact__icon" viewBox="0 0 16 16" aria-hidden="true"><path d="M3.5 1l2.5 3-1.5 2c.8 1.8 2.2 3.2 4 4l2-1.5 3 2.5-1.5 2.5C6.5 13.5 2.5 9.5 1 2.5z"/></svg>
          555-214-7730
        </li>
        <li class="contact__item">
          <svg class="contact__icon" viewBox="0 0 16 16" aria-hidden="true"><rect x="4" y="1" width="8" height="4"/><rect x="1" y="6" width="14" height="6" rx="1"/><rect x="4" y="10" width="8" height="5"/></svg>
          555-214-7731
        </li>
        <li class="contact__item">
          <svg class="contact__icon" viewBox="0 0 16 16" aria-hidden="true"><path d="M1 4h14v9H1z M1 4l7 5 7-5" stroke="#5f6778" stroke-width="1.2"/></svg>
          name@quarrystonedev.com
        </li>
        <li class="contact__item">
          <svg class="contact__icon" viewBox="0 0 16 16" aria-hidden="true"><circle cx="8" cy="8" r="7"/><path d="M5 4c2 1 1 3 3 3s1 3 3 4M9 2c0 2 2 2 4 3" stroke="#5f6778" stroke-width="1.4" fill="none"/></svg>
          www.quarrystonedev.com
        </li>
      </ul>
    </div>
    <div class="card__stripe"></div>
  </section>

  <section class="card card--back">
    <div class="back-mark">QUARRYSTONE</div>
    <div class="back-web">www.quarrystonedev.com</div>
  </section>
</div>
</body>
</html>
```